SaaS Early tech startup business card design

Unique design for experience ecommerce platform company. the business cards will be used by executive members. conformance with color code is required.

```html
<!DOCTYPE html>
<html lang="en">
<head>
<meta charset="utf-8">
<title>lumo — business card</title>
<link href="https://fonts.googleapis.com/css2?family=Lexend:wght@700&family=Roboto:wght@400&display=swap" rel="stylesheet">
<style>
  :root {
    --bg: #6b6868;
    --teal: #13a393;
    --teal-dark: #0d7774;
    --navy: #0f4f7c;
    --paper: #f7f7f6;
    --ink: #3a3a3a;
    --white: #ffffff;
  }
  * { margin: 0; padding: 0; box-sizing: border-box; }
  html, body { width: 1200px; height: 1200px; overflow: hidden; }
  body { background: var(--bg); position: relative; font-family: "Roboto", sans-serif; }

  .card {
    position: absolute;
    left: 280px;
    width: 640px;
    height: 378px;
    border-radius: 26px;
    overflow: hidden;
  }
  .card svg.card-art { position: absolute; inset: 0; width: 100%; height: 100%; }

  /* Front */
  .card--front { top: 190px; background: var(--teal); }
  .front-brand {
    position: absolute; left: 0; right: 0; top: 126px;
    text-align: center; color: var(--white);
  }
  .brand-name {
    font-family: "Lexend", sans-serif; font-weight: 700;
    font-size: 116px; line-height: 1; letter-spacing: -2px;
  }

  /* Back */
  .card--back { top: 636px; background: var(--paper); }
  .back-brand { position: absolute; left: 54px; top: 70px; }
  .back-brand .brand-name { color: var(--navy); font-size: 110px; }

  .holder { position: absolute; right: 44px; top: 56px; text-align: right; }
  .holder-name {
    font-family: "Lexend", sans-serif; font-weight: 700;
    font-size: 27px; color: var(--teal-dark); letter-spacing: -0.5px;
  }
  .holder-role { font-size: 16px; color: var(--ink); margin-top: 2px; }

  .contact-list {
    position: absolute; right: 44px; top: 248px;
    list-style: none; color: var(--white); font-size: 16.5px;
    text-align: right;
  }
  .contact-list li { height: 24px; display: flex; justify-content: flex-end; align-items: center; gap: 13px; }
  .contact-list li.address { margin-top: 3px; }
  .contact-list svg { width: 17px; height: 17px; }
</style>
</head>
<body>

<section class="card card--front" aria-label="Card front">
  <svg class="card-art" viewBox="0 0 640 378" preserveAspectRatio="none" aria-hidden="true">
    <defs>
      <linearGradient id="frontShade" x1="0" y1="0" x2="1" y2="1">
        <stop offset="0" stop-color="#0f8a84"/>
        <stop offset="1" stop-color="#0b6f6e"/>
      </linearGradient>
    </defs>
    <rect width="640" height="378" fill="var(--teal)"/>
    <path d="M0,52 C120,10 260,20 360,60 C470,104 560,118 620,90 C640,80 640,60 640,40 L640,378 L560,378 C480,340 380,350 330,260 C290,190 230,150 150,160 C80,170 30,210 0,250 Z" fill="url(#frontShade)"/>
    <path d="M0,0 L640,0 L640,40 C620,20 560,30 480,24 C380,14 260,0 140,6 C80,10 30,24 0,40 Z" fill="#14958c" opacity="0.7"/>
  </svg>
  <div class="front-brand">
    <div class="brand-name">lumo</div>
  </div>
</section>

<section class="card card--back" aria-label="Card back">
  <svg class="card-art" viewBox="0 0 640 378" preserveAspectRatio="none" aria-hidden="true">
    <path d="M0,330 C120,372 250,310 360,262 C460,220 540,198 640,206 L640,378 L0,378 Z" fill="var(--navy)"/>
    <path d="M0,306 C140,350 260,292 360,248 C460,206 540,184 640,190 L640,200 C540,196 460,220 368,258 C268,300 140,356 0,318 Z" fill="var(--teal)"/>
    <path d="M54,300 C140,320 220,316 320,284 C230,326 140,330 54,300 Z" fill="var(--teal)"/>
  </svg>

  <div class="back-brand">
    <div class="brand-name">lumo</div>
  </div>

  <div class="holder">
    <div class="holder-name">Rami K.</div>
    <div class="holder-role">CTO/Owner</div>
  </div>

  <ul class="contact-list">
    <li><span>(00) 0111 LUMO</span>
      <svg viewBox="0 0 20 20" aria-hidden="true"><path d="M2,8 C2,4 18,4 18,8 L14,9 L13,7 L7,7 L6,9 Z" fill="#fff"/><path d="M5,10 L15,10 L17,17 L3,17 Z" fill="#fff"/><circle cx="10" cy="13" r="2" fill="var(--navy)"/></svg></li>
    <li><span>info@lumo.net</span>
      <svg viewBox="0 0 20 20" aria-hidden="true"><rect x="2" y="4" width="16" height="12" fill="#fff"/><path d="M2,4 L10,11 L18,4 M2,16 L8,10 M18,16 L12,10" stroke="var(--navy)" stroke-width="1.4" fill="none"/></svg></li>
    <li><span>www.lumo.net</span>
      <svg viewBox="0 0 20 20" aria-hidden="true"><circle cx="10" cy="10" r="7.5" fill="#fff"/><g stroke="var(--navy)" stroke-width="1" fill="none"><ellipse cx="10" cy="10" rx="3.2" ry="7.5"/><path d="M2.5,10 H17.5 M4,6 H16 M4,14 H16"/></g></svg></li>
    <li class="address"><span>Crescent Plaza, Dubai, UAE</span></li>
  </ul>
</section>

</body>
</html>
```